Business Card Design

I need a logo and a business card design that can be used for my business stationary, Facebook page and in the future a website. I don't know if I need a large design for brochures and stationery and a small portion of that as the logo or business card design. I probably need some advice about that. My new company is called Willowbank Family Circle. I don't have all of my business contact details available yet, but I want to get the design ready, so that when all this information is available I can get the printing done quickly.I'm a social worker and my business will be providing parenting groups and counselling sessions for parents.I would like the logo and business card to be very feminine and pretty. I want a silhouette image of a Mother and Baby and decorative swirls of flowers/vines/leaves and butterflies.I have found some designs elsewhere that are along the lines of what I am looking for. These images are attached below, but the quality of these attachments is very poor as I photographed them with my phone.My preferred colours would be to use black and white, purple and/or pink, aqua and or blue/green.There are four logo/business card options attached. Logo option 1 - I really like the flower and vine design. Logo option 2 - again I like the flowers and leaf design and the use of colour and the silhouette image of the Mum and Baby; Logo option 3 - I like the butterflies and decorative swirls in this option and Logo option 4 - I think this design is the best for a logo. I love the mother and baby image. I don't like the tree branch and the birds but I like the way the hair has been incorporated into the branch. I prefer the design of the flowers/vine/leaves in the other options.

Industry/Entity Type

Business

Contact Information for Business Card

Company Name:Embrace Attachment ParentingMobile:0417 751 394Email:Currently sourcing - TBAContact Name:Janelle ApplegarthQualifications:Currently sourcing details - TBA

Font styles to use
Script

Colors
33a6d7
85cae6
886aae
6c459b
e667a6
eea4c8

Requirements
Must have
• My project must have an image of a mother and child, slightly encircled by the mother's hair perhaps in a heart shape, and the mother's hair becoming a beautiful filigree design of vine/leaves/flowers and with some butterfly somewhere.
• Can all of the Words be in the same font Attachment Parenting can be slightly smaller.
Nice to have
• I would like to also have a similar vine/leaves/flowers and maybe a butterfly on the opposite side of the card. Maybe the Mother/child image on the top left of the card and the other pattern on the bottom right.
• If possible the use of aqua, purple and pink.

```html
<!DOCTYPE html>
<html lang="en">
<head>
<meta charset="utf-8">
<title>Willowbank Family Circle – Business Card</title>
<link rel="stylesheet" href="https://fonts.googleapis.com/css2?family=Open+Sans:wght@400&family=Playfair+Display:wght@700&display=swap">
<style>
  :root {
    --card-bg: #ffffff;
    --frame: #1a9aa3;
    --teal-dark: #12707e;
    --teal-bright: #17a0a6;
    --teal-text: #1a8a99;
    --mark-faint: #dbe9eb;
    --ink: #3b3b3b;
    --band-dark: #3a3a3a;
  }
  * { margin: 0; padding: 0; box-sizing: border-box; }
  html, body {
    width: 1200px; height: 686px; overflow: hidden; background: var(--card-bg);
  }
  .card {
    position: relative; width: 1200px; height: 686px;
    background: var(--card-bg); border: 1px solid var(--frame); overflow: hidden;
  }
  .brand-mark-faint {
    position: absolute; left: 717px; top: 100px; width: 460px; height: 460px;
    border-radius: 50%; background: var(--mark-faint);
  }
  .brand-mark {
    position: absolute; left: 248px; top: 30px; width: 200px; height: 200px;
    border-radius: 50%; background: var(--teal-dark);
  }
  .brand-name {
    position: absolute; left: 0; width: 696px; top: 270px; text-align: center;
    font-family: "Playfair Display", Georgia, serif; font-weight: 700;
    font-size: 56px; line-height: 62px; color: var(--teal-dark);
  }
  .brand-rule {
    position: absolute; left: 0; top: 416px; width: 679px; height: 9px;
    background: var(--teal-bright);
  }
  .contact {
    position: absolute; left: 34px; display: flex; align-items: center;
    font-family: "Open Sans", Arial, sans-serif; font-size: 28px; color: var(--ink);
  }
  .contact svg { width: 50px; height: 50px; margin-right: 52px; flex: none; }
  .contact-email { top: 458px; }
  .contact-phone { top: 545px; }
  .person {
    position: absolute; left: 700px; width: 480px; text-align: center;
    font-family: "Open Sans", Arial, sans-serif;
  }
  .person-name { top: 340px; font-size: 48px; color: var(--ink); }
  .person-role { top: 406px; font-size: 23px; color: var(--teal-text); }
  .footer-bands { position: absolute; left: 0; bottom: 0; width: 1200px; height: 47px; }
</style>
</head>
<body>
<main class="card">
  <div class="brand-mark-faint" role="img" aria-label="Faint brand emblem decoration"></div>
  <div class="brand-mark" role="img" aria-label="Willowbank Family Circle emblem"></div>

  <h1 class="brand-name">Willowbank<br>Family Circle</h1>
  <div class="brand-rule"></div>

  <p class="contact contact-email">
    <svg viewBox="0 0 50 50" aria-hidden="true">
      <rect x="1" y="10" width="48" height="32" fill="var(--teal-bright)"/>
      <path d="M1 10 L25 30 L49 10" fill="none" stroke="#fff" stroke-width="2.5"/>
      <path d="M1 42 L19 25 M49 42 L31 25" fill="none" stroke="#fff" stroke-width="2"/>
    </svg>
    Curreently Sourcing
  </p>
  <p class="contact contact-phone">
    <svg viewBox="0 0 50 50" aria-hidden="true">
      <path d="M8 4 L18 4 L22 16 L15 21 C18 29 22 33 30 36 L35 29 L47 33 L47 43 C47 46 44 48 40 47 C22 43 7 28 3 10 C2 6 4 4 8 4 Z" fill="var(--teal-bright)"/>
    </svg>
    0438 260 517
  </p>

  <h2 class="person person-name">Rosalind Thackeray</h2>
  <p class="person person-role">(DIRECTOR)</p>

  <svg class="footer-bands" viewBox="0 0 1200 47" preserveAspectRatio="none" aria-hidden="true">
    <polygon points="0,0 893,0 871,47 0,47" fill="var(--teal-dark)"/>
    <polygon points="907,0 1200,0 1200,47 887,47" fill="var(--band-dark)"/>
  </svg>
</main>
</body>
</html>
```